RK Donnelly & Associates

Create a website encompassing design work already carried out for business card.
Small accounting practice, business accounting and management, superannuation, audit, taxation.

```html
<!DOCTYPE html>
<html lang="en">
<head>
<meta charset="utf-8">
<title>RK Donnelly &amp; Associates</title>
<link href="https://fonts.googleapis.com/css2?family=Libre+Baskerville&family=PT+Sans:wght@400;700&display=swap" rel="stylesheet">
<style>
:root{
  --dark:#1f1f20;
  --dark-2:#262728;
  --blue:#6aa6dc;
  --blue-light:#a9d6f2;
  --blue-deep:#4f8fcc;
  --ink:#222;
  --text:#555;
  --rule:#e2e2e2;
  --white:#fff;
}
*{margin:0;padding:0;box-sizing:border-box}
html,body{width:900px;height:1200px;overflow:hidden;background:var(--white)}
body{position:relative;font-family:"PT Sans",Arial,sans-serif;color:var(--text)}
.abs{position:absolute}
.serif{font-family:"Libre Baskerville",Georgia,serif}

.site-header{left:0;top:0;width:900px;height:94px;background:var(--dark)}
.brand{left:106px;top:20px;display:flex;align-items:center;gap:9px}
.brand-mark{width:30px;height:30px;background:var(--blue)}
.brand-name{font-family:"Libre Baskerville",Georgia,serif;color:var(--white);font-size:14px;line-height:16px}
.nav{top:29px;left:0;height:35px;font-size:10px;color:var(--white);text-transform:uppercase}
.nav a{position:absolute;top:0;height:35px;line-height:35px;color:var(--white);text-decoration:none;white-space:nowrap}
.nav .active{left:402px;width:60px;background:var(--blue);text-align:center;border-radius:2px}
.nav .active::after{content:"";position:absolute;left:26px;bottom:-5px;border:5px solid transparent;border-bottom:0;border-top-color:var(--blue)}

.tagband{left:0;top:94px;width:900px;height:24px;background:var(--blue);color:var(--white);font-size:8.5px;font-weight:700;line-height:24px;padding-left:110px}

.hero{left:0;top:118px;width:900px;height:358px;background:var(--dark-2)}
.hero-panel{left:106px;top:144px;width:688px;height:267px;border-radius:6px;background:radial-gradient(ellipse at 45% 55%,#bfe6f8 0%,#92cbee 50%,#6ba9dc 100%)}
.hero-kicker{left:163px;top:186px;font-size:17px;color:var(--ink)}
.hero-title{left:162px;top:214px;font-size:37px;color:var(--ink);letter-spacing:.5px}
.hero-lead{left:162px;top:266px;font-size:22px;line-height:24px;color:var(--white)}
.hero-btn{left:170px;top:334px;width:103px;height:35px;background:var(--dark);color:var(--white);font-size:11px;line-height:35px;text-align:center;border-radius:2px}
.hero-art{left:530px;top:150px;width:185px;height:250px;border-radius:4px;background:radial-gradient(ellipse at 50% 55%,rgba(255,255,255,.55),rgba(255,255,255,0) 70%)}
.dots{left:421px;top:439px;display:flex;gap:7px}
.dots span{width:9px;height:9px;border-radius:50%;background:var(--white)}
.dots span:first-child{background:var(--blue)}

.section-title{left:106px;font-size:18px;color:var(--ink);text-transform:uppercase}
.section-title em{font-style:normal;color:var(--blue)}
.rule{left:106px;width:689px;height:1px;background:var(--rule)}

.photo{background:linear-gradient(135deg,#d9dde0,#8c9197 60%,#3a3d42)}
.welcome-text{left:278px;top:559px;width:517px;font-size:8.6px;line-height:16.8px;color:#444;text-align:justify}
.btn{background:var(--blue);color:var(--white);font-size:8.5px;text-align:center;text-transform:uppercase}
.welcome-btn{left:279px;top:650px;width:70px;height:26px;line-height:26px}

.card{top:748px;width:125px;height:203px;border:1px solid #ddd;text-align:center}
.card svg{position:absolute;left:30px;top:8px}
.card h3{position:absolute;left:0;width:100%;font-family:"Libre Baskerville",Georgia,serif;font-weight:400;font-size:10.5px;line-height:13px;color:var(--ink);text-transform:uppercase}
.card p{position:absolute;left:8px;right:8px;top:118px;font-size:8.6px;line-height:15.5px;color:#555}
.card .btn{position:absolute;left:39px;top:165px;width:46px;height:26px;line-height:26px}

.arrows{left:752px;top:977px;font-size:20px;color:#ccc;letter-spacing:4px}
.quote{font-size:8.6px;line-height:16.8px;color:#666;text-align:justify}
.quote cite{display:block;font-style:normal;color:var(--blue)}

.site-footer{left:0;top:1139px;width:900px;height:61px;background:var(--blue)}
.copyright{left:106px;top:1165px;font-size:8.5px;color:var(--white);text-transform:uppercase}
.social{top:1157px;width:23px;height:23px}
</style>
</head>
<body>

<header class="abs site-header">
  <div class="abs brand">
    <span class="brand-mark"></span>
    <span class="brand-name">RK Donnelly<br>&amp; Associates.</span>
  </div>
  <nav class="abs nav">
    <a class="active" href="#">Home</a>
    <a href="#" style="left:478px">About Us</a>
    <a href="#" style="left:549px">Projects</a>
    <a href="#" style="left:619px">Services</a>
    <a href="#" style="left:695px">Blog</a>
    <a href="#" style="left:754px">Contact</a>
  </nav>
</header>

<div class="abs tagband">Accountant · Business Solutions · Management · Superannuation · Audit</div>

<section class="abs hero"></section>
<div class="abs hero-panel"></div>
<div class="abs hero-kicker serif">RK Donnelly &amp;</div>
<div class="abs hero-title serif">ASSOCIATES</div>
<div class="abs hero-lead serif">Irtor eu nisi ferm entum sempe<br>luctus lareet retrum.</div>
<div class="abs hero-btn serif">READ MORE</div>
<div class="abs hero-art" role="img" aria-label="Illustration of a white umbrella under falling raindrops"></div>
<div class="abs dots"><span></span><span></span><span></span><span></span></div>

<h2 class="abs section-title serif" style="top:505px">Welcome to <em>RK Donnelly &amp; Associates</em></h2>
<div class="abs rule" style="top:532px"></div>
<div class="abs photo" style="left:106px;top:560px;width:149px;height:115px" role="img" aria-label="Photo of a businesswoman working at a laptop"></div>
<p class="abs welcome-text">Cras metus erat, ullamcorper id euismod dapibus, adipiscing ultricies felis. Nulla id metus dictum tellus posuere volutpat placerat lobortis ante. Sed lacinia viverra pulvinar. Nam ut justo vel quam imperdiet elementum molestie non arcu. Suspendisse tincidunt blandit sem, in facilisis quam tempus eu. In placerat nunc libero, at convallis quam. Pellentesque habitant morbi tristique senectus et netus et malesuada fames ac turpis egestas. Cras metus erat, ullamcorper id euismod dapibus, adipiscing ultricies felis. Nulla id metus dictum tellus posuere volutpat placerat lobortis ante. Sed lacinia viverra pulvinar.</p>
<div class="abs btn welcome-btn">Read More</div>

<h2 class="abs section-title serif" style="top:697px">Our <em>Services</em></h2>
<div class="abs rule" style="top:724px"></div>

<div class="abs card" style="left:106px">
  <svg width="64" height="64" viewBox="0 0 64 64"><circle cx="32" cy="32" r="32" fill="#6aa6dc"/><circle cx="32" cy="32" r="27" fill="none" stroke="#fff" stroke-width="1.2"/><circle cx="32" cy="24" r="5" fill="#fff"/><rect x="22" y="31" width="20" height="13" rx="2" fill="#fff"/></svg>
  <h3 style="top:85px">Accounting<br>Practice</h3>
  <p>Cras metus erat, ullamcor per id euismod dapibus adipiscing ultricies felis.</p>
  <div class="btn">More</div>
</div>
<div class="abs card" style="left:247px">
  <svg width="64" height="64" viewBox="0 0 64 64"><circle cx="32" cy="32" r="32" fill="#6aa6dc"/><circle cx="32" cy="32" r="27" fill="none" stroke="#fff" stroke-width="1.2"/><rect x="23" y="18" width="18" height="26" rx="2" fill="none" stroke="#fff" stroke-width="2"/><path d="M27 36h10M27 40h10" stroke="#fff" stroke-width="1.6"/><text x="32" y="32" font-size="11" font-family="Arial" font-weight="700" fill="#fff" text-anchor="middle">$</text></svg>
  <h3 style="top:85px">Business<br>Accounting</h3>
  <p>Cras metus erat, ullamcor per id euismod dapibus adipiscing ultricies felis.</p>
  <div class="btn">More</div>
</div>
<div class="abs card" style="left:389px">
  <svg width="64" height="64" viewBox="0 0 64 64"><circle cx="32" cy="32" r="32" fill="#6aa6dc"/><circle cx="32" cy="32" r="27" fill="none" stroke="#fff" stroke-width="1.2"/><rect x="20" y="35" width="5" height="8" fill="#fff"/><rect x="27" y="31" width="5" height="12" fill="#fff"/><rect x="34" y="33" width="5" height="10" fill="#fff"/><rect x="41" y="27" width="5" height="16" fill="#fff"/><path d="M20 31l8-7 6 4 10-9" fill="none" stroke="#fff" stroke-width="2"/></svg>
  <h3 style="top:92px">Superannuation</h3>
  <p>Cras metus erat, ullamcor per id euismod dapibus adipiscing ultricies felis.</p>
  <div class="btn">More</div>
</div>
<div class="abs card" style="left:530px">
  <svg width="64" height="64" viewBox="0 0 64 64"><circle cx="32" cy="32" r="32" fill="#6aa6dc"/><circle cx="32" cy="32" r="27" fill="none" stroke="#fff" stroke-width="1.2"/><rect x="23" y="19" width="18" height="26" rx="2" fill="none" stroke="#fff" stroke-width="2"/><rect x="28" y="16" width="8" height="5" fill="#fff"/><path d="M27 27h10M27 32h10M27 37h10M27 41h10" stroke="#fff" stroke-width="1.5"/></svg>
  <h3 style="top:92px">Audit</h3>
  <p>Cras metus erat, ullamcor per id euismod dapibus adipiscing ultricies felis.</p>
  <div class="btn">More</div>
</div>
<div class="abs card" style="left:669px">
  <svg width="64" height="64" viewBox="0 0 64 64"><circle cx="32" cy="32" r="32" fill="#6aa6dc"/><circle cx="32" cy="32" r="27" fill="none" stroke="#fff" stroke-width="1.2"/><rect x="20" y="24" width="24" height="15" rx="2" transform="rotate(-15 32 32)" fill="#fff"/><circle cx="32" cy="32" r="4" fill="#6aa6dc"/></svg>
  <h3 style="top:92px">Taxation</h3>
  <p>Cras metus erat, ullamcor per id euismod dapibus adipiscing ultricies felis.</p>
  <div class="btn">More</div>
</div>

<h2 class="abs section-title serif" style="top:976px">Our <em>Testimonials</em></h2>
<div class="abs arrows">‹ ›</div>
<div class="abs rule" style="top:1004px"></div>

<div class="abs photo" style="left:106px;top:1032px;width:76px;height:67px" role="img" aria-label="Portrait photo of a smiling man in a suit"></div>
<blockquote class="abs quote" style="left:200px;top:1028px;width:234px">“Simply dummy text of the printing and typesetting industry. Lorem Ipsum has been the industry's standard dummy text ever since the 1500s, when an unknown printer took a galley of type and scrambled it to make a type specimen book”.<cite>-Sam Reed</cite></blockquote>

<div class="abs photo" style="left:451px;top:1032px;width:76px;height:67px" role="img" aria-label="Portrait photo of a smiling woman"></div>
<blockquote class="abs quote" style="left:545px;top:1029px;width:247px">“Simply dummy text of the printing and typesetting industry. Lorem Ipsum has been the industry's standard dummy text ever since the 1500s, when an unknown printer took a galley of type and scrambled it to make a type specimen book.”<cite>-Ana Lowe</cite></blockquote>

<footer class="abs site-footer"></footer>
<div class="abs copyright">Copyright 2014. RK Donnelly &amp; Associates . All rights reserved.</div>
<a class="abs social" href="#" aria-label="Social profile" style="left:710px;background:#2f5f9e"></a>
<a class="abs social" href="#" aria-label="Social profile" style="left:741px;background:#3aa9de"></a>
<a class="abs social" href="#" aria-label="Social profile" style="left:771px;background:#2b79b5"></a>

</body>
</html>
```